Web Design job: SaaS start-up needs a cutting-edge web design

What's Needed:
- All designs files created
- Fully coded implementation in HTML/CSS/Bootstrap
- Pages: 5 -- see content here http://www.TeamVerdexa.com
-- Home Page
-- The Hidden Value
-- Benefits
-- About us
-- Careers
- The existing site has the textual content for each page. We can tweak to meet specific designs if needed.
- You will need to update/create image and interactive content for pages.

Reference:
Our existing website has a lot of content on it for reference -
http://www.TeamVerdexa.com

Description:
We need a web design that focuses in the UX and conveys the idea of magically fixing company problems by way of using our software.

Home Page
The main goal is to Drive Sales of the SaaS tool. When a visitor lands on our home page they should see: What we do, How we can help their problem and How to contact us.
1. Quickly understand What We Do
-- we sell SaaS software.
-- Need to quickly convey what our software does. It's seems complicated but really its not. See the description in about us for more info and visit our existing site.

2. How we can help their problem
-- We aim to solve any problem related to employees
-- Even if the visitor does not have a specific problem in mind, there are several areas organizations can always improve: (some examples below)
---- Create Stronger, More Productive Teams
---- Build Better Communications Pathways
---- Encourage Innovation and Positive Change
---- Develop and Retain Strong "Company Culture"

3. Be able to Contact Us to get started
-- contacting us to get a sales lead is the ultimate goal.
-- the user should not have to hunt to contact us. needs to be easy.

Other Pages (Hidden Value, Benefit, About Us, Careers):
-- These are informative pages about our software and process.
-- If we grab the attention of the user on the home page then these are the pages that they will explore for more info.
-- Should be able to link to these pages from the main nav or from sections with the homepage. For example: What We Do sections could link to the benefits page. How we help their problem sections could link to the Hidden Value page. Regardless of what links to where, the idea is that we will be able to nav to other areas.

About Us:
Our company name is TeamVerdexa (as in Organizational Analysis). We provide a software as a service (SaaS) that uses a simple 6-question survey to analyze the relationships of people within an Organization and provide leaders with ground-breaking Insights about their teams, interactive social network data visualizations to explore their team's composition and we give detailed profiles of the key players (i.e, who are the Social Bridges, Who are the Knowledge Bottlenecks, Who are the Best Mentors, Who are the people that are completely disconnected/out of the loop). Leaders then use this information to make high level organizational decisions.

What's unique about our software:
-- Powerful analysis results from just a 6-question "pulse-surveys"
-- Innovative Tools for visually exploring the organization through relationships as opposed to org-chart
-- Get real-time results as opposed to waiting months with traditional methods
-- Traditional Org-charts represent the organization's skeleton, whereas we uncover the organization's neural network (how it solves problems).

Preferred fonts (but could be convinced otherwise if looks great):
-- Section titles - Aleo
-- Main body - Lato
-- TeamVerdexa logo - Philosopher

Things we like:
-- We like a big slider as the top of the landing page.

Colors to include:
-- Colors in the logo (red, blue, green, teal) as accent colors

Feel of the site:
-- Cutting-edge Software
-- Professional
-- Social Network flare (we analyze relationships)

Note:
If we find a great match with a designer there is strong possibility to continue the relationship with follow on work redesigning our web-based application.

Target Market(s)

Current customers are Morrow Pike & Fenwell, Clearbrook Valley Bank.
We target anyone that manages a large team. Such as Corporate Leaders, High Level Managers, HR Leaders

Industry/Entity Type

Business Software

Contact Information for Business Card

Logo image
Name of company "TEAMVERDEXA" In Philosopher font.
Tagline: "Unlock the Hidden Value In Your Teams"
Person's Name, Title, email, phone.

Coding

Coded - Design and coding required

Number of Pages Required

4 page

Font styles to use
Other font styles liked:
• Lato, Philosopher, Aero

Colors
ec1f27
0255a3

Requirements
Must have
• See description.
Nice to have
• Things we like:
• We like a big slider as the top of the landing page. Ours is a little clunky and outdated but something fresh and sleek would be great.
• Colors to include:
• We would like to use the colors in the logo as accent colors in the site to give a consistent look and feel.
• Feel of the site:
• Cutting-edge Software
• Professional
• Social Network flare (we analyze relationships)

```html
<!DOCTYPE html>
<html lang="en">
<head>
<meta charset="utf-8">
<title>TeamVerdexa — Home</title>
<link href="https://fonts.googleapis.com/css2?family=Lato:wght@300;400;700&family=Montserrat:wght@400;600;700&display=swap" rel="stylesheet">
<style>
:root{
  --blue:#1e4c9c;
  --blue-dark:#0f4a9e;
  --red:#e8292c;
  --green:#9cc43a;
  --teal:#5fb8d6;
  --ink:#2b2b2b;
  --muted:#555;
  --line:#dcdcdc;
  --gray:#f1f1f1;
  --white:#fff;
}
*{box-sizing:border-box;margin:0;padding:0}
html,body{width:1200px;height:3416px;overflow:hidden}
body{font-family:"Lato",sans-serif;color:var(--ink);background:var(--white);position:relative}
.abs{position:absolute}
section,header,footer{position:absolute;left:0;width:1200px}
.heading{font-family:"Montserrat",sans-serif;font-weight:400;color:var(--blue)}
.rule{height:3px;width:52px;background:var(--teal)}

/* header */
.site-header{top:0;height:130px;background:var(--white)}
.brand{left:130px;top:18px;width:200px;height:100px}
.brand-mark{position:absolute;left:62px;top:6px;width:48px;height:48px;border-radius:50%;background:var(--red)}
.brand-name{position:absolute;left:0;top:66px;font-family:"Lato",sans-serif;font-weight:400;font-size:26px;color:var(--blue);letter-spacing:1px;white-space:nowrap}
.phone-icon{left:440px;top:22px;width:30px;height:30px;border:1px solid var(--line);border-radius:50%}
.office{top:18px;font-size:11px;color:var(--muted);line-height:16px}
.office b{display:block;font-weight:400;font-size:15px;color:var(--blue);margin-top:4px}
.office-divider{top:20px;width:1px;height:34px;background:var(--line)}
.main-nav{top:80px;left:437px;display:flex;height:38px;align-items:center;font-size:13px}
.main-nav a{color:var(--ink);text-decoration:none;padding:0 17px;height:38px;line-height:38px}
.main-nav a.active{background:var(--blue);color:var(--white)}
.main-nav a.login{border:1px solid var(--line);color:var(--blue);margin-left:24px;height:38px}

/* hero */
.hero{top:130px;height:507px;background:linear-gradient(180deg,#ececec,#f4f4f4)}
.hero-art{left:130px;top:40px;width:520px;height:410px;background:radial-gradient(ellipse at 45% 40%,#ffffff 0,#e4e6ea 55%,#d3d6db 100%);border-radius:6px}
.hero-title{left:717px;top:70px;font-family:"Montserrat",sans-serif;font-weight:700;font-size:29px;line-height:34px;color:var(--blue)}
.hero-list{left:724px;top:172px;list-style:none;font-size:14px;color:var(--muted)}
.hero-list li{height:33px;padding-left:18px;position:relative}
.hero-list li::before{content:"";position:absolute;left:0;top:6px;width:7px;height:7px;border-radius:50%;background:var(--teal)}
.btn-red{background:var(--red);color:var(--white);font-family:"Montserrat",sans-serif;font-weight:600;font-size:15px;text-align:center}
.hero-btn{left:724px;top:370px;width:198px;height:52px;line-height:52px}
.slide-arrow{top:232px;width:36px;height:44px;background:var(--blue)}

/* what we do */
.what{top:637px;height:654px;background:var(--white)}
.what .heading{left:130px;top:42px;font-size:28px}
.what .rule{left:130px;top:88px}
.what-lead{left:130px;top:124px;width:560px;font-size:13.5px;line-height:22px}
.features{left:130px;top:217px;width:530px;height:353px}
.feature{position:absolute;width:265px;height:176px;text-align:center;font-size:14px}
.feature svg{display:block;margin:54px auto 12px}
.feature.b{left:265px;border-left:1px solid var(--line)}
.feature.c{top:176px;border-top:1px solid var(--line)}
.feature.d{left:265px;top:176px;border-left:1px solid var(--line);border-top:1px solid var(--line)}
.feature.c,.feature.a{text-align:left}
.feature.a svg,.feature.c svg{margin-left:50px}
.network-art{left:695px;top:23px;width:455px;height:580px;border-radius:50%;background:radial-gradient(circle at 45% 40%,rgba(230,60,80,.35),rgba(140,80,220,.25) 45%,rgba(90,120,230,.12) 70%,rgba(255,255,255,0) 75%)}

/* about */
.about{top:1291px;height:554px;background:var(--gray)}
.about-panel{left:132px;top:0;width:453px;height:554px;background:var(--blue-dark);color:var(--white)}
.about-panel h2{position:absolute;left:52px;top:66px;font-family:"Montserrat",sans-serif;font-weight:400;font-size:24px}
.about-panel p{position:absolute;left:52px;top:130px;width:240px;font-size:12.5px;line-height:21.5px;text-align:justify}
.unique-card{left:540px;top:64px;width:526px;height:437px;background:var(--white);box-shadow:0 2px 10px rgba(0,0,0,.08)}
.unique-card h3{position:absolute;left:42px;top:38px;font-family:"Montserrat",sans-serif;font-weight:600;font-size:15px;color:var(--blue)}
.unique-item{position:absolute;left:40px;width:440px;height:60px;font-size:13.5px;line-height:20px}
.unique-item .ico{position:absolute;left:0;top:0;width:46px;height:46px;border:1px solid #9aa8c4;border-radius:50%}
.unique-item p{position:absolute;left:70px;top:2px;width:370px}

/* help */
.help{top:1845px;height:637px;background:var(--white)}
.help .heading{left:0;width:1200px;top:58px;text-align:center;font-size:28px}
.help .rule{left:574px;top:110px}
.help-art{left:137px;top:135px;width:398px;height:433px;border-radius:50%;background:conic-gradient(from 20deg,var(--red),var(--green),var(--blue),var(--teal),var(--red));opacity:.85}
.help-item{left:588px;width:470px;font-size:13.5px;line-height:20px}
.help-item .ico{position:absolute;left:0;top:0;width:44px;height:44px;border-radius:50%;border:1px solid}
.help-item p{position:absolute;left:100px;top:2px;width:370px}
.help-list{left:700px;top:423px;list-style:none;font-size:12.5px}
.help-list li{height:37px;padding-left:22px;position:relative}
.help-list li::before{content:"";position:absolute;left:0;top:4px;width:8px;height:8px;border-radius:50%;background:var(--blue)}

/* contact */
.contact{top:2482px;height:597px;background:linear-gradient(135deg,#e9eaec,#f2f2f2 50%,#e6e8ea)}
.contact .heading{left:0;width:1200px;top:58px;text-align:center;font-size:28px}
.contact-sub{left:0;width:1200px;top:100px;text-align:center;font-size:14px}
.col-title{top:180px;font-family:"Montserrat",sans-serif;font-weight:600;font-size:20px;color:var(--blue)}
.col-rule{top:216px;height:3px;width:175px;background:var(--blue)}
.location{width:260px;font-size:12px;line-height:26px}
.location h4{font-weight:700;font-size:14px;margin-bottom:10px}
.field{left:645px;width:421px;background:var(--white);border:1px solid #cfcfcf;font-size:12px;color:var(--muted);padding:10px 14px}
.submit{left:961px;top:2496px}

/* footer */
.site-footer{top:3079px;height:337px;background:var(--white)}
.foot-brand{left:130px;top:40px;width:230px;height:150px}
.foot-brand .brand-mark{left:80px;top:4px;width:62px;height:62px}
.foot-brand .brand-name{left:0;top:96px;font-size:30px}
.foot-divider{left:478px;top:40px;width:1px;height:150px;background:var(--line)}
.foot-label{left:610px;font-size:11px;letter-spacing:1px;color:var(--ink)}
.foot-links{left:610px;top:93px;font-size:12px;color:var(--ink)}
.foot-links span{color:#999;padding:0 6px}
.social{top:172px;width:32px;height:32px;border-radius:50%}
.foot-rule{left:130px;top:234px;width:940px;height:1px;background:var(--line)}
.copyright{left:0;width:1200px;top:278px;text-align:center;font-size:11px;color:var(--muted)}
</style>
</head>
<body>

<header class="site-header">
  <div class="abs brand"><span class="brand-mark"></span><span class="brand-name">TEAMVERDEXA</span></div>
  <svg class="abs phone-icon" viewBox="0 0 30 30"><path d="M11 9c1 3 4 8 9 11l2-2 2 2-2 3c-6-1-12-8-13-14l3-2 2 2z" fill="none" stroke="var(--blue)" stroke-width="1.3"/></svg>
  <div class="abs office" style="left:496px">Birmingham<b>205-555-0148</b></div>
  <div class="abs office-divider" style="left:636px"></div>
  <div class="abs office" style="left:656px">Chicago<b>719-555-0172</b></div>
  <div class="abs office-divider" style="left:796px"></div>
  <div class="abs office" style="left:815px">Birmingham<b>205-555-0148</b></div>
  <div class="abs office-divider" style="left:958px"></div>
  <div class="abs office" style="left:979px">Denver<b>719-555-0172</b></div>
  <nav class="abs main-nav">
    <a class="active">Home</a><a>The Hidden Value</a><a>Benefits</a><a>About Us</a><a>Careers</a><a class="login">&#9633; Client Login</a>
  </nav>
</header>

<section class="hero">
  <div class="abs hero-art" role="img" aria-label="Desktop, tablet and phone screens showing the network analysis dashboard over a faint world map"></div>
  <h1 class="abs hero-title">Fast and Easy<br>Assessments</h1>
  <ul class="abs hero-list">
    <li>Simple Data Collection (6 Questions)</li>
    <li>Proven World-Class Algorithms</li>
    <li>Real-time Visual Exploration Capabilities</li>
    <li>Immediate Analyses and 24/7 Cloud-based Access</li>
    <li>Full Support and Guidance from our Experts</li>
  </ul>
  <div class="abs btn-red hero-btn">EXAMPLE RESULTS</div>
  <svg class="abs slide-arrow" style="left:0" viewBox="0 0 36 44"><path d="M21 15l-7 7 7 7" fill="none" stroke="#fff" stroke-width="2.5"/></svg>
  <svg class="abs slide-arrow" style="left:1164px" viewBox="0 0 36 44"><path d="M15 15l7 7-7 7" fill="none" stroke="#fff" stroke-width="2.5"/></svg>
</section>

<section class="what">
  <h2 class="abs heading">What We Do</h2>
  <div class="abs rule"></div>
  <p class="abs what-lead">FIRST Data-Driven Platform with Innovative Tools for Dynamic, Real-Time Analyses and Exploration of Employee Relationships</p>
  <div class="abs features">
    <div class="feature a">
      <svg width="66" height="56" viewBox="0 0 66 56"><rect x="3" y="3" width="60" height="40" rx="3" fill="none" stroke="var(--blue)" stroke-width="2.5"/><path d="M25 43v8h16v-8M18 53h30" fill="none" stroke="var(--blue)" stroke-width="2.5"/><rect x="13" y="12" width="6" height="5" fill="var(--red)"/><rect x="13" y="24" width="6" height="5" fill="var(--red)"/><path d="M24 14h26M24 26h26" stroke="var(--blue)" stroke-width="2"/></svg>
      <div style="margin-left:20px">Online Pulse Survey</div>
    </div>
    <div class="feature b">
      <svg width="60" height="56" viewBox="0 0 60 56"><rect x="22" y="3" width="16" height="12" fill="none" stroke="var(--blue)" stroke-width="2.5"/><path d="M30 15v10M10 25h40M10 25v8M30 25v8M50 25v8" fill="none" stroke="var(--blue)" stroke-width="2.5"/><rect x="3" y="33" width="14" height="11" fill="none" stroke="var(--blue)" stroke-width="2.5"/><rect x="23" y="33" width="14" height="11" fill="none" stroke="var(--blue)" stroke-width="2.5"/><rect x="43" y="33" width="14" height="11" fill="none" stroke="var(--red)" stroke-width="2.5"/></svg>
      Proprietary Algorithms
    </div>
    <div class="feature c">
      <svg width="54" height="60" viewBox="0 0 54 60" style="margin-top:40px"><path d="M14 26V17a13 13 0 0 1 26 0v9" fill="none" stroke="var(--blue)" stroke-width="3"/><rect x="5" y="26" width="44" height="30" rx="8" fill="none" stroke="var(--blue)" stroke-width="3"/><circle cx="27" cy="39" r="5" fill="var(--red)"/><path d="M27 43v6" stroke="var(--red)" stroke-width="3"/></svg>
      <div>Organizational Key Insights</div>
    </div>
    <div class="feature d">
      <svg width="62" height="60" viewBox="0 0 62 60" style="margin-top:40px"><rect x="3" y="3" width="24" height="16" rx="4" fill="var(--red)"/><rect x="35" y="3" width="24" height="16" rx="4" fill="var(--blue)"/><circle cx="15" cy="34" r="7" fill="none" stroke="var(--blue)" stroke-width="2.5"/><circle cx="47" cy="34" r="7" fill="none" stroke="var(--red)" stroke-width="2.5"/><path d="M3 58c0-9 5-13 12-13s12 4 12 13M35 58c0-9 5-13 12-13s12 4 12 13" fill="none" stroke="var(--blue)" stroke-width="2.5"/></svg>
      Expert Review and Action Plans
    </div>
  </div>
  <div class="abs network-art" role="img" aria-label="Colourful social network graph of connected employee nodes"></div>
</section>

<section class="about">
  <div class="abs about-panel">
    <h2>About Us</h2>
    <p>Our company name is TeamVerdexa (as in Organizational Analysis). We provide a software as a service (SaaS) that uses a simple 6-question survey to analyze the relationships of people within an Organization and provide leaders with ground-breaking Insights about their teams, interactive social network data visualizations to explore their team's composition and we give detailed profiles of the key players (i.e, who are the Social Bridges, Who are the Knowledge Bottlenecks, Who are the Best Mentors, Who are the people that are completely disconnected/out of the loop). Leaders then use this information to make high level organizational decisions.</p>
  </div>
  <div class="abs unique-card">
    <h3>What's unique about our software:</h3>
    <div class="unique-item" style="top:88px"><svg class="ico" viewBox="0 0 46 46"><path d="M12 24h6l3-7 4 12 3-5h6" fill="none" stroke="var(--blue)" stroke-width="1.6"/></svg><p>Powerful analysis results from just a 6-question "pulse-surveys"</p></div>
    <div class="unique-item" style="top:170px"><svg class="ico" viewBox="0 0 46 46"><path d="M15 31l16-16M15 15l16 16" stroke="var(--blue)" stroke-width="1.8"/></svg><p>Innovative Tools for visually exploring the organization through relationships as opposed to org-chart</p></div>
    <div class="unique-item" style="top:252px"><svg class="ico" viewBox="0 0 46 46"><path d="M14 32V14M14 32h18M18 28v-4M23 28v-7M28 28v-10" fill="none" stroke="var(--blue)" stroke-width="1.8"/></svg><p>Get real-time results as opposed to waiting months with traditional methods</p></div>
    <div class="unique-item" style="top:334px"><svg class="ico" viewBox="0 0 46 46"><rect x="13" y="14" width="20" height="14" fill="none" stroke="var(--blue)" stroke-width="1.6"/><path d="M19 32h8" stroke="var(--blue)" stroke-width="1.6"/></svg><p>Traditional Org-charts represent the organization's skeleton, whereas we uncover the organization's neural network (how it solves problems).</p></div>
  </div>
</section>

<section class="help">
  <h2 class="abs heading">How we can help</h2>
  <div class="abs rule"></div>
  <div class="abs help-art" role="img" aria-label="Abstract figures in red, green, blue and teal joined in a circle"></div>
  <div class="abs help-item" style="top:138px"><svg class="ico" viewBox="0 0 44 44" style="border-color:var(--red)"><circle cx="15" cy="20" r="3" fill="var(--red)"/><circle cx="22" cy="18" r="3" fill="var(--red)"/><circle cx="29" cy="20" r="3" fill="var(--red)"/><path d="M11 30h22" stroke="var(--red)" stroke-width="2"/></svg><p style="left:100px">We aim to solve any problem related<br>to employees</p></div>
  <div class="abs help-item" style="top:238px"><svg class="ico" viewBox="0 0 44 44" style="border-color:var(--green)"><circle cx="22" cy="22" r="5" fill="none" stroke="var(--green)" stroke-width="1.8"/><path d="M22 10v5M22 29v5M10 22h5M29 22h5" stroke="var(--green)" stroke-width="1.8"/></svg><p>Even if the visitor does not have a specific problem in mind, there are several areas organizations can always improve: (some examples below)</p></div>
  <ul class="abs help-list">
    <li>Create Stronger, More Productive Teams</li>
    <li>Build Better Communications Pathways</li>
    <li>Encourage Innovation and Positive Change</li>
    <li>Develop and Retain Strong "Company Culture"</li>
  </ul>
</section>

<section class="contact" role="region" aria-label="Contact section over a faint road map">
  <h2 class="abs heading">Contact us</h2>
  <p class="abs contact-sub">Questions, Demos or Custom Quotes</p>
  <h3 class="abs col-title" style="left:130px">Our Four Locations</h3>
  <div class="abs col-rule" style="left:130px"></div>
  <div class="abs location" style="left:130px;top:258px"><h4>Cincinnati, OH</h4>T : 908-555-0193<br>E : cincinnati@teamverdexa.com</div>
  <div class="abs location" style="left:408px;top:258px"><h4>Denver, CO</h4>T : 719-555-0172<br>E : denver@teamverdexa.com</div>
  <div class="abs location" style="left:130px;top:393px"><h4>Birmingham, AL</h4>T : 205-555-0148<br>E : birmingham@teamverdexa.com</div>
  <div class="abs location" style="left:408px;top:393px"><h4>Chicago, IL</h4>T : 719-555-0172<br>E : chicago@teamverdexa.com</div>
  <h3 class="abs col-title" style="left:645px">Or send us a message</h3>
  <div class="abs col-rule" style="left:645px;width:220px"></div>
  <div class="abs field" style="top:244px;height:36px">Name</div>
  <div class="abs field" style="top:296px;height:38px">E mail</div>
  <div class="abs field" style="top:348px;height:124px">Message</div>
  <div class="abs btn-red" style="left:961px;top:496px;width:105px;height:42px;line-height:42px">SUBMIT</div>
</section>

<footer class="site-footer">
  <div class="abs brand foot-brand"><span class="brand-mark"></span><span class="brand-name">TEAMVERDEXA</span></div>
  <div class="abs foot-divider"></div>
  <div class="abs foot-label" style="top:66px">MENU</div>
  <div class="abs foot-links">Home<span>|</span>The Hidden Value<span>|</span>Benefits<span>|</span>About Us<span>|</span>Careers<span>|</span>Client Login</div>
  <div class="abs foot-label" style="top:140px">FOLLOW US</div>
  <div class="abs social" style="left:610px;background:var(--blue)"></div>
  <div class="abs social" style="left:651px;background:var(--teal)"></div>
  <div class="abs social" style="left:692px;background:var(--red)"></div>
  <div class="abs social" style="left:733px;background:var(--blue-dark)"></div>
  <div class="abs foot-rule"></div>
  <p class="abs copyright">Copyrights © 2016 All Rights Reserved</p>
</footer>

</body>
</html>
```